Business Card Design For Marketing Agnecy LVP

Need business card design for marketing agency.

Doug Fenwick
President, CEO
1-555-302-4196
doug@boldpromoperksgroup.example
www.BoldPromoPerksGroup.example

Back Side:
Boost Sales Using Rewards, Incentives & Giveaways
Get A Free Sample Package

Target Market(s)

B2B

Industry/Entity Type

Marketing

Contact Information for Business Card

Doug Fenwick
President, CEO
1-555-302-4196

Back Side:
Get A Free Sample Package

Please note that my current url is OLD DESIGN. I am working on new design and want the business card to match color themes at least on new site. Here is the demo link for new site so you can see the colors I use, etc.

http://layoutcratehub.example/kq/doug/lvp_final/index.html

Requirements
Must have
• Please note that my current url is OLD DESIGN. I am working on new design and want the business card to match color themes at least on new site. Here is the demo link for new site so you can see the colors I use, etc.

Nice to have

Should not have

```html
<!DOCTYPE html>
<html lang="en">
<head>
<meta charset="utf-8">
<title>LVP Business Card – Front and Back</title>
<link rel="stylesheet" href="https://fonts.googleapis.com/css2?family=Bebas+Neue&family=Josefin+Sans:wght@300;400;600&family=Montserrat:wght@800&display=swap">
<style>
  :root {
    --page-bg: #e8e8e8;
    --card-bg: #f3f3f3;
    --brand-blue: #1b6db0;
    --brand-green: #43a148;
    --ink-grey: #4a4a4c;
    --white: #ffffff;
  }
  * { margin: 0; padding: 0; box-sizing: border-box; }
  html, body {
    width: 1200px; height: 1200px; overflow: hidden;
    background: var(--page-bg);
  }
  .card {
    position: absolute; left: 227px; width: 746px; height: 425px;
    background: var(--card-bg); overflow: hidden;
  }
  .card--front { top: 135px; }
  .card--back { top: 639px; }

  /* Front */
  .wordmark {
    position: absolute; left: 0; right: 0; top: 50px;
    text-align: center; color: var(--brand-blue);
    font-family: "Montserrat", sans-serif; font-weight: 800;
  }
  .wordmark__initials { font-size: 104px; line-height: 1; letter-spacing: 2px; }
  .wordmark__name { font-size: 19px; letter-spacing: 1.5px; margin-top: 12px; }

  .stripe-green { position: absolute; left: 0; right: 0; top: 247px; height: 19px; background: var(--brand-green); }
  .band-blue { position: absolute; left: 0; right: 0; bottom: 0; background: var(--brand-blue); }
  .card--front .band-blue { top: 271px; }
  .card--back .band-blue { top: 253px; }

  .badge { position: absolute; left: 173px; width: 400px; height: 100px; }
  .card--front .badge { top: 244px; }
  .card--back .badge { top: 228px; }
  .badge svg { position: absolute; inset: 0; }
  .badge__text { position: absolute; left: 0; right: 0; text-align: center; color: var(--white); }

  .holder-name {
    top: 17px; font-family: "Josefin Sans", sans-serif; font-weight: 600;
    font-size: 29px; letter-spacing: 1px;
  }
  .holder-title {
    top: 52px; font-family: "Josefin Sans", sans-serif; font-weight: 300; font-size: 22px;
  }
  .contact-line {
    position: absolute; left: 0; right: 0; top: 368px;
    display: flex; justify-content: center; align-items: center; gap: 12px;
    color: var(--white); font-family: "Josefin Sans", sans-serif; font-weight: 300; font-size: 21px;
  }
  .contact-item { display: flex; align-items: center; gap: 14px; }
  .contact-item svg { width: 18px; height: 18px; }

  /* Back */
  .wordmark-row {
    position: absolute; left: 0; right: 0; top: 40px;
    display: flex; justify-content: center; align-items: center; gap: 22px;
    color: var(--brand-blue); font-family: "Montserrat", sans-serif; font-weight: 800;
  }
  .wordmark-row__initials { font-size: 62px; line-height: 1; }
  .wordmark-row__name { font-size: 25px; line-height: 1.15; letter-spacing: 1px; }

  .tagline {
    position: absolute; left: 0; right: 0; top: 148px; text-align: center;
    font-family: "Bebas Neue", sans-serif; color: var(--ink-grey); font-size: 26px; letter-spacing: 0.3px;
  }
  .tagline__accent { font-size: 33px; }
  .tagline__accent--green { color: var(--brand-green); }
  .tagline__accent--blue { color: var(--brand-blue); }

  .offer {
    top: 24px; font-family: "Bebas Neue", sans-serif; font-size: 36px; letter-spacing: 0.5px;
  }
  .site-url {
    position: absolute; left: 0; right: 0; top: 359px; text-align: center;
    color: var(--white); font-family: "Bebas Neue", sans-serif; font-size: 27px; letter-spacing: 0.3px;
  }
</style>
</head>
<body>

<section class="card card--front">
  <div class="wordmark">
    <div class="wordmark__initials">LVP</div>
    <div class="wordmark__name">BOLD PROMO PERKS GROUP</div>
  </div>

  <div class="stripe-green"></div>
  <div class="band-blue"></div>

  <div class="badge">
    <svg viewBox="0 0 400 100" width="400" height="100">
      <path d="M3 3 H397 L391 76 Q390 86 380 87 L200 99 L20 87 Q10 86 9 76 Z"
            fill="var(--brand-green)" stroke="var(--white)" stroke-width="4" stroke-linejoin="round"/>
    </svg>
    <div class="badge__text holder-name">DOUG FENWICK</div>
    <div class="badge__text holder-title">President, CEO</div>
  </div>

  <div class="contact-line">
    <span class="contact-item">
      <svg viewBox="0 0 20 20" aria-hidden="true">
        <circle cx="10" cy="10" r="10" fill="var(--white)"/>
        <path d="M5 8 Q10 4 15 8 L14 10 L12 9 L12 8 Q10 7 8 8 L8 9 L6 10 Z M6.5 11 H13.5 L14 15 H6 Z" fill="var(--brand-blue)"/>
        <circle cx="10" cy="13" r="1.3" fill="var(--white)"/>
      </svg>
      1-555-302-4196
    </span>
    <span class="contact-item">
      <svg viewBox="0 0 20 20" aria-hidden="true">
        <circle cx="10" cy="10" r="10" fill="var(--white)"/>
        <rect x="5" y="6.5" width="10" height="7" fill="none" stroke="var(--brand-blue)" stroke-width="1.3"/>
        <path d="M5 6.5 L10 11 L15 6.5" fill="none" stroke="var(--brand-blue)" stroke-width="1.3"/>
      </svg>
      doug@boldpromoperksgroup.example
    </span>
  </div>
</section>

<section class="card card--back">
  <div class="wordmark-row">
    <span class="wordmark-row__initials">LVP</span>
    <span class="wordmark-row__name">BOLD PROMO<br>PERKS GROUP</span>
  </div>

  <p class="tagline">
    <span class="tagline__accent tagline__accent--green">Boost</span>
    Sales Using Rewards, Incentives &amp;
    <span class="tagline__accent tagline__accent--blue">Giveaways</span>
  </p>

  <div class="band-blue"></div>

  <div class="badge">
    <svg viewBox="0 0 400 100" width="400" height="100">
      <path d="M3 3 Q3 0 8 0 H392 Q397 0 397 3 L391 76 Q390 86 380 87 L200 99 L20 87 Q10 86 9 76 Z"
            fill="var(--brand-green)" stroke="var(--white)" stroke-width="4" stroke-linejoin="round"/>
    </svg>
    <div class="badge__text offer">GET A FREE SAMPLE PACKAGE</div>
  </div>

  <div class="site-url">WWW.BOLDPROMOPERKSGROUP.EXAMPLE</div>
</section>

</body>
</html>
```